Christmas Banner for frontpage of website

New online scarf store just opened needs a Christmas Banner stating Free Delivery (UK only). Also if it could incorporate guaranteed Christmas delivery if ordered before 18th (might be too wordy though?) I would really like it to bring some colour to the page. The page is currently black and white with a pink accent and is very simple which is why I would like something modern and elegant, simple but with some colour. It is a shopify store I understand the banner size should be 950px by 290px the website is www.tolvarenshop.co.uk

Target Market(s)

Ladies

Industry/Entity Type

Store

Requirements
Should not have
• Not to look tacky.

```html
<!DOCTYPE html>
<html lang="en">
<head>
<meta charset="utf-8">
<title>Tolvaren – Scarves</title>
<link rel="stylesheet" href="https://fonts.googleapis.com/css2?family=Arimo:wght@400;700&family=PT+Serif&family=Open+Sans:ital,wght@1,400;1,700;1,800&family=Fira+Sans+Extra+Condensed:ital,wght@1,400&display=swap">
<style>
  :root {
    --ink: #2b2428;
    --brand: #4a3a3c;
    --muted: #8a8a8a;
    --rule: #e6e0da;
    --accent: #d0197f;
    --topbar: #3a3550;
    --title: #5a4e52;
    --festive-red: #e0203a;
    --cream: #f7f2ec;
    --paper: #ffffff;
  }
  * { box-sizing: border-box; margin: 0; padding: 0; }
  html, body { width: 1200px; height: 823px; overflow: hidden; background: var(--paper); }
  body { position: relative; font-family: "Arimo", Arial, sans-serif; color: var(--ink); }

  .top-strip { position: absolute; left: 0; top: 0; width: 1200px; height: 4px; background: var(--topbar); }

  .utility-bar { position: absolute; left: 31px; top: 4px; width: 1139px; height: 40px; border-bottom: 1px solid var(--rule); font-size: 11.5px; }
  .utility-bar > * { position: absolute; top: 14px; display: flex; align-items: center; gap: 6px; }
  .search { left: 9px; color: var(--muted); font-size: 12.5px; top: 13px; }
  .login { left: 294px; }
  .signup { left: 349px; }
  .cart { left: 964px; }
  .cart .count { color: var(--accent); }
  .cart-divider { left: 1058px; top: 11px; width: 1px; height: 16px; background: var(--rule); }
  .checkout { left: 1080px; }

  .brand-name { position: absolute; left: 40px; top: 78px; font-family: "PT Serif", Georgia, serif; font-size: 31px; color: var(--brand); font-weight: 400; }
  .tagline { position: absolute; right: 39px; top: 89px; font-family: "PT Serif", Georgia, serif; font-size: 14px; color: var(--brand); }

  .side-nav { position: absolute; left: 40px; top: 152px; width: 196px; list-style: none; border-top: 1px solid var(--rule); }
  .side-nav li { height: 34.7px; line-height: 34px; border-bottom: 1px solid var(--rule); font-size: 11px; font-weight: 700; color: var(--brand); }
  .side-nav li:last-child { border-bottom: none; }

  .social { position: absolute; left: 40px; top: 378px; display: flex; gap: 6.5px; }
  .social span { width: 22px; height: 22px; border-radius: 50%; background: var(--brand); }

  .content-rule { position: absolute; left: 325px; top: 152px; width: 836px; height: 1px; background: var(--rule); }

  .promo-banner { position: absolute; left: 316px; top: 171px; width: 845px; height: 258px; overflow: hidden; background: var(--cream); }
  .promo-decor { position: absolute; left: 0; top: 0; width: 845px; height: 258px;
    background:
      linear-gradient(180deg, rgba(247,242,236,0) 0%, rgba(247,242,236,0) 100%),
      linear-gradient(90deg, #5f7f3e 0%, #8a5a3c 9%, #c9a66a 15%, rgba(247,242,236,0) 22%),
      linear-gradient(180deg, rgba(122,150,90,0.55) 0%, rgba(247,242,236,0) 22%);
  }
  .promo-photo { position: absolute; left: 500px; top: 0; width: 345px; height: 258px;
    background: linear-gradient(90deg, rgba(247,242,236,0) 0%, #dfe3e6 10%, #bcc3c8 30%, #b8a294 55%, #d9c2b3 72%, #d95a5e 100%); }
  .promo-copy { position: absolute; left: 165px; top: 62px; width: 360px; }
  .promo-title { font-family: "Open Sans", Arial, sans-serif; font-style: italic; font-weight: 800; font-size: 54px; line-height: 1; color: var(--title); letter-spacing: -1.2px; white-space: nowrap; }
  .promo-sub { margin: 6px 0 0 2px; font-family: "Fira Sans Extra Condensed", Arial, sans-serif; font-style: italic; font-weight: 400; font-size: 30px; line-height: 1.1; color: var(--festive-red); letter-spacing: -0.5px; white-space: nowrap; }
  .promo-note { margin: 2px 0 0 128px; font-family: "Open Sans", Arial, sans-serif; font-style: italic; font-weight: 400; font-size: 17px; color: var(--ink); white-space: nowrap; }
  .order-button { position: absolute; left: 311px; top: 186px; width: 168px; height: 39px; border-radius: 20px; background: var(--festive-red);
    color: #fff; font-family: "Open Sans", Arial, sans-serif; font-style: italic; font-weight: 700; font-size: 19px; display: flex; align-items: center; justify-content: center; }

  .product { position: absolute; top: 476px; width: 267px; text-align: center; }
  .product .photo { width: 267px; height: 267px; }
  .product .name { margin-top: 13px; font-size: 11px; color: var(--ink); }
  .product .price { margin-top: 5px; font-family: "PT Serif", Georgia, serif; font-size: 14.5px; color: var(--ink); }
  .product.featured .name { color: var(--accent); }
  .product-1 { left: 343px; }
  .product-1 .photo { width: 184px; height: 258px; margin: 5px auto 4px; border-radius: 50%; background: linear-gradient(160deg, #2f7a62, #7a4a66 55%, #2a6a58); }
  .product-2 { left: 627px; }
  .product-2 .photo { background: linear-gradient(135deg, #d8dada, #e8e9e9 50%, #d4d6d6); }
  .product-3 { left: 912px; }
  .product-3 .photo { width: 240px; height: 250px; margin: 9px auto 8px; border-radius: 40% 40% 8px 8px; background: linear-gradient(180deg, #c41e55, #b0244a 70%, #8a3a7a); }
</style>
</head>
<body>
  <div class="top-strip"></div>

  <header class="utility-bar">
    <div class="search">
      <svg width="11" height="11" viewBox="0 0 12 12"><circle cx="5" cy="5" r="3.6" fill="none" stroke="#2b2428" stroke-width="1.8"/><line x1="7.6" y1="7.6" x2="11" y2="11" stroke="#2b2428" stroke-width="2"/></svg>
      Search
    </div>
    <div class="login">Login</div>
    <div class="signup">Sign Up</div>
    <div class="cart">
      <svg width="17" height="13" viewBox="0 0 17 13"><path d="M0 1h3l2 8h9l2-6H4.5" fill="none" stroke="#2b2428" stroke-width="1.6"/><circle cx="6" cy="11.5" r="1.3" fill="#2b2428"/><circle cx="13" cy="11.5" r="1.3" fill="#2b2428"/></svg>
      My Cart <span class="count">(0)</span>
    </div>
    <div class="cart-divider"></div>
    <div class="checkout">Check Out</div>
  </header>

  <div class="brand-name">Tolvaren</div>
  <div class="tagline">FREE DELIVERY - Love Your Neck</div>

  <ul class="side-nav">
    <li>Home</li>
    <li>Funky Scarves</li>
    <li>Thicker Scarves</li>
    <li>Thin Scarves</li>
    <li>Blog</li>
    <li>About Us</li>
  </ul>

  <div class="social" aria-label="Social links">
    <span></span><span></span><span></span><span></span><span></span>
  </div>

  <div class="content-rule"></div>

  <section class="promo-banner">
    <div class="promo-decor" role="img" aria-label="Christmas greenery with baubles along the left and top edges"></div>
    <div class="promo-photo" role="img" aria-label="Couple in winter scarves and knitted hat"></div>
    <div class="promo-copy">
      <div class="promo-title">Free Delivery</div>
      <div class="promo-sub">Guaranteed Christmas delivery</div>
      <div class="promo-note">if ordered before 18th</div>
    </div>
    <div class="order-button">Order Now</div>
  </section>

  <article class="product product-1 featured">
    <div class="photo" role="img" aria-label="Multicoloured chunky knit snood"></div>
    <div class="name">Elin Snood</div>
    <div class="price">£10.50</div>
  </article>
  <article class="product product-2">
    <div class="photo" role="img" aria-label="Light grey scarf with swallow print"></div>
    <div class="name">Mira Scarf</div>
    <div class="price">£9.75</div>
  </article>
  <article class="product product-3">
    <div class="photo" role="img" aria-label="Pink and red striped fringed scarf"></div>
    <div class="name">Tova scarf</div>
    <div class="price">£9.75</div>
  </article>
</body>
</html>
```